Business Card and Letterhead for Pimlu - modern real estate business

I need a double sided business card design for Pimlu. Please see business card brief here https://files.trelvonadocs.com/sheet/r/7QzTmWbaXLJnoPEd-kRyUgFhHsstbvCe2qfoMxDa_pz/view?mode=shared

Please feel free to design the business cards however you feel best. I am happy to give some creative freedoms and then provide feedback from there.

Please then also create a letterhead to match the business card design

Colors

Designer to choose colors to be used in the design.

Requirements
Must have
• Must be a modern, elegant business card which looks very professional

```html
<!DOCTYPE html>
<html lang="en">
<head>
<meta charset="utf-8">
<title>Pimlu Business Card</title>
<link rel="stylesheet" href="https://fonts.googleapis.com/css2?family=EB+Garamond:wght@400;600&display=swap">
<style>
  :root {
    --page: #2a2a2a;
    --card: #000000;
    --red: #e3101f;
    --white: #f2f2f2;
    --photo-dark: #0c0c0c;
    --photo-mid: #3a3a3c;
  }
  * { margin: 0; padding: 0; box-sizing: border-box; }
  html, body { width: 1200px; height: 900px; overflow: hidden; }
  body {
    background: var(--page);
    font-family: "EB Garamond", Georgia, serif;
    position: relative;
  }
  .card {
    position: absolute;
    left: 290px;
    width: 620px;
    height: 354px;
    background: var(--card);
    box-shadow: 0 10px 30px rgba(0,0,0,0.5);
    overflow: hidden;
  }
  .card-front { top: 76px; }
  .card-back { top: 470px; }

  .brand-name {
    position: absolute;
    left: 0; right: 0; top: 50%;
    transform: translateY(-50%);
    text-align: center;
    color: var(--red);
    font-weight: 600;
    font-size: 112px;
    letter-spacing: 10px;
    line-height: 1;
  }

  .agent-photo {
    position: absolute;
    right: 0; top: 0;
    width: 290px; height: 354px;
    background: radial-gradient(ellipse at 55% 60%, var(--photo-mid) 0%, #1e1e20 45%, var(--photo-dark) 75%, var(--card) 100%);
  }

  .agent-block {
    position: absolute;
    left: 44px; top: 96px;
  }
  .agent-name {
    color: var(--red);
    font-size: 24px;
    font-weight: 600;
    letter-spacing: 0.5px;
    line-height: 1;
    text-transform: uppercase;
  }
  .agent-title {
    color: var(--white);
    font-size: 15px;
    text-transform: uppercase;
    letter-spacing: 0.3px;
    margin-top: 4px;
  }
  .agent-rule {
    width: 250px;
    height: 2px;
    background: var(--red);
    margin-top: 4px;
  }
  .agent-web {
    color: var(--white);
    font-size: 13px;
    margin-top: 4px;
    margin-left: 16px;
  }

  .contact-list {
    position: absolute;
    left: 44px; top: 220px;
    list-style: none;
  }
  .contact-item {
    display: flex;
    align-items: center;
    gap: 10px;
    color: var(--white);
    font-size: 16px;
    line-height: 24px;
  }
  .contact-icon { width: 14px; height: 14px; flex: none; }
  .contact-address {
    color: var(--red);
    font-size: 16px;
    font-weight: 600;
    line-height: 20px;
    margin-top: 4px;
  }
</style>
</head>
<body>

<section class="card card-front" aria-label="Card front">
  <div class="brand-name">PIMLU</div>
</section>

<section class="card card-back" aria-label="Card back">
  <div class="agent-photo" role="img" aria-label="Portrait photo of the agent in a dark suit"></div>

  <div class="agent-block">
    <div class="agent-name">Liam Carter</div>
    <div class="agent-title">Licenced Real Estate Agent</div>
    <div class="agent-rule"></div>
    <div class="agent-web">www.pimlu.com</div>
  </div>

  <ul class="contact-list">
    <li class="contact-item">
      <svg class="contact-icon" viewBox="0 0 14 14" aria-hidden="true"><rect x="3.5" y="1" width="7" height="12" rx="1.2" fill="none" stroke="#e3101f" stroke-width="1.4"/><circle cx="7" cy="11" r="0.8" fill="#e3101f"/></svg>
      0412 608 391
    </li>
    <li class="contact-item">
      <svg class="contact-icon" viewBox="0 0 14 14" aria-hidden="true"><path d="M1 5 Q7 0 13 5 L11 7 L9 5.5 L5 5.5 L3 7 Z" fill="#e3101f"/><rect x="3" y="7.5" width="8" height="5" rx="1" fill="#e3101f"/></svg>
      1300 547 820
    </li>
    <li class="contact-item">
      <svg class="contact-icon" viewBox="0 0 14 14" aria-hidden="true"><rect x="1" y="3" width="12" height="8.5" fill="#e3101f"/><path d="M1 3 L7 8 L13 3" fill="none" stroke="#000" stroke-width="1"/></svg>
      liam@pimlu.com
    </li>
    <li class="contact-address">PO Box 3917,<br>Bellhaven NSW 2790</li>
  </ul>
</section>

</body>
</html>
```